Webdesign für Heilpraktiker
Zielgruppe
Ich bin Heilpraktiker und betreibe eine Naturheilpraxis mit den Schwerpunkten der traditionellen chinesischen Medizin (TCM). Da ganz besonders in der Philosophie (sogenannte 'Schule' des Wo Shen). Aber auch in der traditionellen Heilweise der TCM, wie Akupunktur, Heilkräutermedizin und weiteres.
Die Zielgruppe sind Menschen, die medizinische Hilfe benötigen. (Vom Kind bis zum älteren Menschen).
Aufgabenstellung
Es gibt ein Praxislogo, ein Foto von mir und ggf. ein Landschaftsbild. Ich dachte an fünf Hauptseiten mit Untergruppen. Am Ende sollte alles in Wordpress formatiert werden können, um es zu veröffentlichen.
Weitere Fotos zur Unterstützung der Themen kann ich natürlich gerne liefern.
Die Gestaltung ist nicht festgesetzt. Sollte aber seriös rüber kommen.

```html
<!DOCTYPE html>
<html lang="de">
<head>
<meta charset="utf-8">
<title>Naturheilpraxis Wo Shen</title>
<link rel="stylesheet" href="https://fonts.googleapis.com/css2?family=Open+Sans:ital,wght@0,400;1,400&family=EB+Garamond:wght@400&display=swap">
<style>
:root{
  --paper:#f1efeb;
  --paper-dark:#ebe7e1;
  --gold:#c4a45a;
  --gold-light:#d3b774;
  --ink:#3f3d3a;
  --ink-soft:#555250;
  --night:#2b2623;
  --white:#ffffff;
}
*{margin:0;padding:0;box-sizing:border-box}
html,body{width:1200px;height:3372px;overflow:hidden}
body{position:relative;background:var(--paper);font-family:"Open Sans",sans-serif;color:var(--ink)}
.abs{position:absolute}
.serif{font-family:"EB Garamond",serif;font-weight:400;letter-spacing:.5px}

.site-header{left:0;top:0;width:1200px;height:236px;background:linear-gradient(#f3f1ee,#eeebe6)}
.brand{left:0;width:1200px;top:20px;display:flex;flex-direction:column;align-items:center;gap:8px}
.brand-mark{width:64px;height:64px;border-radius:50%;border:2px solid var(--ink)}
.brand-name{font-family:"Open Sans",sans-serif;font-size:20px;color:var(--ink)}
.main-nav{left:0;width:1200px;top:166px;display:flex;justify-content:center;gap:24px;font-size:19px;text-transform:uppercase;color:#222}
.main-nav span:nth-child(3){margin-right:6px}

.hero-photo{left:0;top:236px;width:576px;height:386px;background:linear-gradient(120deg,#b89a5c,#e0c788 45%,#c9a865 75%,#9c7d45)}
.hero-quote{left:576px;top:272px;width:624px;height:350px;background:linear-gradient(135deg,var(--gold-light),var(--gold))}
.quote-text{left:0;top:82px;width:624px;text-align:center;color:var(--white);font-size:23px;line-height:37.5px}
.quote-author{right:80px;top:236px;color:var(--white);font-size:29px;font-style:italic}
.quote-mark{color:var(--white);font-size:30px;font-family:"EB Garamond",serif}

.intro{left:0;top:622px;width:1200px;height:506px;background:var(--paper)}
.intro-text{left:140px;top:168px;width:536px;text-align:center;font-size:19.5px;line-height:37.5px;color:var(--ink-soft)}
.intro-photo{left:727px;top:104px;width:360px;height:364px;border-radius:48% 48% 40% 40%/40% 40% 48% 48%;background:radial-gradient(circle at 40% 60%,#8a6236,#c5a170 45%,#e8dfcf 70%,rgba(241,239,235,0) 72%)}

.services{left:0;top:1128px;width:1200px;height:1113px;background:linear-gradient(#ebe7e1,#ece8e2 50%,#eeebe6)}
.service-photo{border-radius:50%}
.service-title{font-size:32px;text-transform:uppercase;color:var(--ink-soft);text-align:center}
.service-text{font-size:16.5px;line-height:30.5px;text-align:center;color:var(--ink-soft)}

.appointment{left:0;top:2241px;width:1200px;height:472px;background:var(--paper)}
.appointment h2,.appointment h3{font-size:29px;color:var(--ink-soft);text-transform:uppercase;text-align:center;width:1200px;left:0}
.hours{left:0;width:1200px;top:197px;text-align:center;font-size:19.5px;line-height:37.3px;color:var(--ink-soft)}

.book{left:0;top:2713px;width:1200px;height:307px;background:linear-gradient(135deg,var(--gold-light),var(--gold))}
.book-cover{left:281px;top:53px;width:142px;height:211px;background:linear-gradient(#ecd9b6,#e2c99f);box-shadow:0 1px 3px rgba(0,0,0,.15)}
.book-title{left:400px;width:600px;top:52px;text-align:center;color:var(--white);font-size:31px;text-transform:uppercase}
.book-text{left:400px;width:600px;top:128px;text-align:center;color:var(--white);font-size:15.5px;line-height:22px}
.book-link{left:400px;width:600px;top:208px;text-align:center;color:var(--white);font-size:22px}

.site-footer{left:0;top:3020px;width:1200px;height:352px;background:var(--night)}
.footer-badge{left:543px;top:31px;width:176px;height:176px;border-radius:50%;background:var(--white);display:flex;align-items:center;justify-content:center;text-align:center;font-size:18px;color:var(--ink);line-height:26px}
.footer-links{left:0;width:1200px;top:278px;display:flex;justify-content:center;gap:18px;color:var(--white);font-size:20px}
</style>
</head>
<body>

<header class="site-header abs">
  <div class="brand abs">
    <div class="brand-mark"></div>
    <div class="brand-name">Praxis Wo Shen</div>
  </div>
  <nav class="main-nav abs">
    <span>Startseite</span><span>Zu meiner Person</span><span>Wobei kann ich helfen</span><span>Was ist das Wo Shen</span><span>Kontakt</span>
  </nav>
</header>

<div class="hero-photo abs" role="img" aria-label="Altes chinesisches Buch mit Akupunktur-Zeichnung"></div>
<section class="hero-quote abs">
  <p class="quote-text abs"><span class="quote-mark">“</span>…die Dinge in Ordnung zu halten ist einfacher<br>als sie wieder in Ordnung zu bringen;<br>die gesunden Menschen vor Krankheiten zu<br>schützen ist eine gefällige Aufgabe für den Arzt<span class="quote-mark">”</span></p>
  <p class="quote-author abs">Meister Lun</p>
</section>

<section class="intro abs">
  <p class="intro-text abs">Vor über vor über 2000 Jahren entstand die traditionelle Heilkunst (TCM) und umfasst<br>therapeutische Verfahren, wie die Akupunktur, die Kräuterheilkunde, das Moxen und Schröpfen, so wie die Ernährungslehre nach den 5 Elementen.</p>
  <div class="intro-photo abs" role="img" aria-label="Schale mit chinesischen Heilkräutern und Akupunkturmodell"></div>
</section>

<section class="services abs">
  <div class="service-photo abs" style="left:200px;top:96px;width:212px;height:212px;background:radial-gradient(circle at 35% 45%,#e7c3ad,#b78a74 50%,#3a3a3c 80%)" role="img" aria-label="Akupunkturnadeln in der Hand"></div>
  <h2 class="service-title serif abs" style="left:490px;width:600px;top:88px">Akupunktur</h2>
  <p class="service-text abs" style="left:470px;width:640px;top:151px">Lorem ipsum dolor sit amet, consectetur adipiscing elit, sed do eiusmod tempor incididunt ut labore et dolore magna aliqua. Quis ipsum suspendisse ultrices gravida. Risus commodo viverra maecenas accumsan lacus vel facilisis.</p>

  <h2 class="service-title serif abs" style="left:150px;width:600px;top:429px">Heilkräutermedizin</h2>
  <p class="service-text abs" style="left:150px;width:600px;top:501px">Lorem ipsum dolor sit amet, consectetur adipiscing elit, sed do eiusmod tempor incididunt ut labore et dolore magna aliqua. Quis ipsum suspendisse ultrices gravida. Risus commodo viverra maecenas accumsan lacus vel facilisis.</p>
  <div class="service-photo abs" style="left:874px;top:425px;width:215px;height:215px;background:radial-gradient(circle at 60% 40%,#b5433a,#7a4a34 45%,#3b2a22 85%)" role="img" aria-label="Getrocknete chinesische Heilkräuter"></div>

  <div class="service-photo abs" style="left:184px;top:786px;width:214px;height:214px;background:radial-gradient(circle at 50% 55%,#f4d7bf,#e9b68f 55%,#f6eee6 85%)" role="img" aria-label="Schröpfgläser auf dem Rücken"></div>
  <h2 class="service-title serif abs" style="left:425px;width:600px;top:784px">Schröpfen</h2>
  <p class="service-text abs" style="left:420px;width:610px;top:837px">Lorem ipsum dolor sit amet, consectetur adipiscing elit, sed do eiusmod tempor incididunt ut labore et dolore magna aliqua. Quis ipsum suspendisse ultrices gravida. Risus commodo viverra maecenas accumsan lacus vel facilisis.</p>
</section>

<section class="appointment abs">
  <h2 class="serif abs" style="top:54px">Vereinbaren Sie einen Termin</h2>
  <h3 class="serif abs" style="top:155px">Öffnungszeiten</h3>
  <p class="hours abs">Montag 8.00 – 13.00 Uhr und 14.00 – 18.00 Uhr<br>Dienstag und Mittwoch 8.00 – 14.00 Uhr<br>Donnerstag 8.00 – 13.00 Uhr und 14.00 – 18.00 Uhr<br>Freitag 8.00 – 14.00 Uhr<br>und nach Vereinbarung</p>
</section>

<section class="book abs">
  <div class="book-cover abs" role="img" aria-label="Buchcover zum Wo Shen"></div>
  <h2 class="book-title serif abs">Buchempfehlung zu Wo Shen</h2>
  <p class="book-text abs">Das erste Wo Shen, das konkrete praktische Methoden beschreibt,<br>wie wir Schwierigkeiten in allen Lebensbereichen lösen können.</p>
  <p class="book-link serif abs">Mehr erfahren</p>
</section>

<footer class="site-footer abs">
  <div class="footer-badge abs">Praxis<br>Wo Shen</div>
  <nav class="footer-links abs"><span>IMPRESSUM</span><span>DATENSCHUTZ</span></nav>
</footer>

</body>
</html>
```